IV Nutritional Clinic Web Design

We are working with Velqo. They are an IV Nutritional Clinic and in need of a new website design.
Some sites to use for inspiration:
https://brightpathcareco.com
https://www.ourzavrowellness.com
https://www.dewspringlounge.com
https://qvitalsurge.com
https://www.lumo-vital.com/pages/iv-therapy-west-hollywood
https://www.tqoncologyhub.com/cancer-care/iv-drips/
https://dripwellary.com
https://corvinahealthhub.com
Thank you for taking the time to consider designing a website for us. We are web developers based in Stockton, CA, USA. Most of our projects go through the same process. Understanding this process may help you win a project with us. We custom-code all of our websites in-house. We don’t have any requirements as to what tools you use for your design, but we prefer Figma files. For any design that we label as four-stars, we send it to the client for review. The client picks the final design they want us to use. Once we complete this process, we will continue to show additional clients all the four-star sites and purchase them later. Your designs will have multiple chances to sell. For better chances of success, we ask that you follow these guidelines.
IMAGES:
If you use any images or icons in the design, we ask that you have a link to the asset so we can purchase the image/icon. Most of the designs we submit do not have the customer’s images on them unless they have some great images. Be creative; show us the feeling you are trying to portray with your image choices. Use any royalty-free site you choose. We subscribe to Pixvane and mainly use their images, but we can purchase images outside of Pixvane.
PLEASE NOTE: we will not submit designs to clients with watermarks on the images.
FONTS:
We ask that you identify the fonts used in the design. This can be done in a message if you want. We typically use Google Fonts and Pixvane Fonts.
CONTENT:
We're always open to different content and ideas. We often submit designs with stock images so the client can see our vision. We typically take pictures after the website launch to use their images with our vision. Lorem Ipsum is fine for paragraphs, but we ask that you write the headers in correct English. We want to be able to show the vision and identify the sections of the website.
INSPIRATION:
We typically add a couple of links in the brief of websites we like to help you get started in your design.
REVISIONS:
We do not often ask for revisions of the designs unless we see something in the design that may not appeal to the client. If there are slight changes that we want to make, we do that in the development process.
FEEDBACK:
We rarely give feedback on designs during the design process. We are working on many website projects and do not have the time to provide feedback. We usually respond if your request is well thought out and asks specific questions, but a note asking “feedback, please” usually goes unanswered.

```html
<!DOCTYPE html>
<html lang="en">
<head>
<meta charset="utf-8">
<title>Velqo Hydration — IV Nutritional Clinic</title>
<link href="https://fonts.googleapis.com/css2?family=Playfair+Display:wght@500;600;700&family=Lexend:wght@300;400;500;600&display=swap" rel="stylesheet">
<style>
:root{
  --navy:#1f2d8c;
  --navy-dark:#16206b;
  --green:#8db255;
  --green-soft:#eef8dc;
  --grey-bg:#f1f2f4;
  --ink:#222;
  --muted:#555;
  --icon-bg:#e3ebfb;
  --footer:#121212;
  --white:#fff;
}
*{box-sizing:border-box;margin:0;padding:0}
html,body{width:1200px;height:4666px;overflow:hidden}
body{font-family:"Lexend",sans-serif;color:var(--ink);background:var(--white);position:relative}
.abs{position:absolute}
section,header,footer{position:absolute;left:0;width:1200px}
.btn{position:absolute;background:var(--green);color:var(--white);font-size:12px;font-weight:500;letter-spacing:.3px;display:flex;align-items:center;justify-content:center;text-transform:uppercase}
.tag{display:flex;align-items:center;justify-content:center;gap:6px;position:absolute}
.tag span{background:var(--navy);color:var(--white);font-size:9px;font-weight:600;letter-spacing:4px;padding:3px 10px 3px 14px}
.section-title{position:absolute;left:0;width:1200px;text-align:center;font-family:"Playfair Display",serif;font-size:27px;font-weight:600;color:#2b2b2b}
.photo{position:absolute}

/* header */
.site-header{top:0;height:100px;z-index:5}
.nav-bar{left:116px;top:22px;width:738px;height:58px;background:var(--white);display:flex;align-items:center;padding-left:14px}
.logo{font-weight:700;font-size:30px;color:var(--navy);letter-spacing:1px;display:flex;align-items:center;gap:8px}
.logo i{display:block;width:10px;height:10px;background:var(--green)}
.nav-links{position:absolute;left:246px;top:22px;display:flex;gap:36px;font-size:12px;color:#555}
.nav-links .active{color:var(--navy);font-weight:500}
.header-btn{left:865px;top:22px;width:218px;height:58px;font-size:12px;gap:12px}

/* hero */
.hero{top:0;height:790px;overflow:hidden}
.hero-bg{left:0;top:0;width:1200px;height:790px;background:linear-gradient(180deg,#9ec3d8 0%,#7fa3b6 30%,#4f7264 55%,#3f5a2c 78%,#34471f 100%)}
.hero h1{left:114px;top:218px;font-family:"Playfair Display",serif;font-size:43px;line-height:58px;color:var(--navy);font-weight:600}
.hero h1 .white{color:var(--white)}
.hero p{left:116px;top:410px;width:380px;font-size:12.5px;line-height:22px;color:var(--white);font-weight:300}
.hero .btn{left:114px;top:507px;width:200px;height:38px}

/* about */
.about{top:790px;height:640px}
.about-text{left:612px;top:133px;width:462px}
.about h2{font-family:"Playfair Display",serif;font-size:26px;font-weight:600;color:#2b2b2b;margin-bottom:20px}
.about p{font-size:11.5px;line-height:22px;color:var(--muted);margin-bottom:18px}
.about .btn{left:612px;top:555px;width:198px;height:40px}

/* services */
.services{top:1430px;height:910px;background:var(--grey-bg)}
.card{position:absolute;width:310px;height:275px;overflow:hidden}
.card .label{position:absolute;left:0;bottom:28px;width:100%;text-align:center;color:var(--white);font-size:17px;font-weight:500}
.card.feature{background:var(--navy)}
.card.feature .frame{position:absolute;left:16px;top:16px;right:16px;bottom:16px;border:1px solid rgba(255,255,255,.55)}
.services .btn{left:501px;top:800px;width:198px;height:42px}

/* benefits */
.benefits{top:2340px;height:640px}
.benefit{position:absolute;width:320px}
.benefit h4{font-size:14px;font-weight:500;color:#222;margin-bottom:8px}
.benefit p{font-size:11px;line-height:20px;color:var(--muted)}
.benefit.left{text-align:right}
.icon-box{position:absolute;width:66px;height:66px;border-radius:14px;background:var(--icon-bg);display:flex;align-items:center;justify-content:center}

/* testimonials */
.testimonials{top:2978px;height:652px;background:var(--green-soft)}
.quote-text{left:693px;top:272px;width:390px;font-size:13px;line-height:28.5px;color:#333;font-weight:300}
.person{left:693px;top:498px}
.person b{display:block;font-size:16px;font-weight:500;color:#222}
.person small{font-size:12px;color:var(--muted)}
.arrow-btn{position:absolute;width:30px;height:30px;border-radius:50%;display:flex;align-items:center;justify-content:center}

/* blog */
.blog{top:3630px;height:600px}
.post{position:absolute;width:308px}
.post .date{display:inline-block;background:var(--navy);color:var(--white);font-size:11px;padding:3px 8px;margin:26px 0 14px}
.post h3{font-size:17px;font-weight:400;line-height:27px;color:#333}
.post .more{display:block;margin-top:34px;font-size:10px;letter-spacing:2.5px;color:#666}

/* footer */
.site-footer{top:4200px;height:466px}
.footer-bg{left:0;top:26px;width:1200px;height:440px;background:var(--footer)}
.footer-logo{left:116px;top:100px;font-size:40px;font-weight:700;color:var(--navy);letter-spacing:2px}
.socials{left:150px;top:190px;display:flex;gap:12px}
.socials span{width:20px;height:20px;border:1.5px solid #ddd;border-radius:3px}
.f-col{position:absolute;top:118px;padding-left:36px;border-left:2px solid var(--green)}
.f-col h5{font-size:12.5px;font-weight:600;color:var(--white);letter-spacing:.5px;margin-bottom:22px;margin-top:-2px}
.f-col li{list-style:none;font-size:12px;color:#ddd;margin-bottom:11px}
.f-col.therapy-list li{font-size:11px;margin-bottom:12.6px}
.contact-row{display:flex;gap:16px;font-size:11.5px;color:#ddd;line-height:20px;margin-bottom:22px}
.copyright{left:0;top:434px;width:1200px;text-align:center;font-size:10px;color:#777}
</style>
</head>
<body>

<!-- HERO -->
<section class="hero">
  <div class="abs hero-bg" role="img" aria-label="Woman in a standing yoga pose on a mat at a mountain viewpoint above a green valley"></div>
  <h1 class="abs">Revitalize Your Body<br>With Customized<br><span class="white">Velqo Hydration.</span></h1>
  <svg class="abs" style="left:462px;top:290px" width="50" height="60" viewBox="0 0 50 60"><path d="M12 4 L15 14 L25 17 L15 20 L12 30 L9 20 L0 17 L9 14Z" fill="var(--green)"/><path d="M34 28 L36 36 L44 38 L36 40 L34 48 L32 40 L24 38 L32 36Z" fill="var(--green)"/></svg>
  <p class="abs">Our specialized IV and injection nutrient therapies deliver essential vitamins, minerals, and amino acids to support your body's optimal function.</p>
  <div class="btn">Book an Appointment</div>
  <svg class="abs" style="left:318px;top:519px" width="22" height="14"><path d="M0 7H14M14 2V12M14 7H22" stroke="var(--green)" stroke-width="3"/></svg>
  <svg class="abs" style="left:0;top:730px" width="1200" height="62" viewBox="0 0 1200 62" preserveAspectRatio="none"><path d="M0 62 L0 55 L80 50 L160 54 L260 46 L380 52 L470 44 L560 48 L640 40 L720 36 L800 30 L900 24 L980 18 L1060 14 L1140 10 L1200 4 L1200 62Z" fill="var(--white)"/></svg>
</section>

<header class="site-header">
  <div class="abs nav-bar"><div class="logo">Velqo<i></i></div>
    <nav class="nav-links"><span class="active">HOME</span><span>ABOUT</span><span>SERVICES</span><span>BENEFITS</span><span>BLOG</span><span>CONTACT</span></nav>
  </div>
  <div class="btn header-btn">
    <svg width="22" height="22" viewBox="0 0 22 22" fill="none" stroke="#fff" stroke-width="1.6"><rect x="2" y="4" width="18" height="16" rx="2"/><path d="M2 9H20M7 2V6M15 2V6"/></svg>
    Book Appointment
  </div>
</header>

<!-- ABOUT -->
<section class="about">
  <div class="photo" style="left:123px;top:72px;width:442px;height:293px;border-radius:10px;background:linear-gradient(120deg,#d8d2c4,#8fb446 45%,#3d4a7a)" role="img" aria-label="Nurse preparing an IV drip for a smiling patient in a green treatment chair"></div>
  <div class="photo" style="left:123px;top:387px;width:219px;height:203px;border-radius:8px;background:linear-gradient(160deg,#e6e8e6,#a6c83a 55%,#d9dcd8)" role="img" aria-label="Green reclining infusion chair in a clinic room"></div>
  <div class="photo" style="left:371px;top:387px;width:181px;height:203px;border-radius:8px;background:linear-gradient(160deg,#efe9e6,#e6a25a 50%,#9cbd5a)" role="img" aria-label="IV bag filled with fresh fruit slices"></div>
  <div class="tag" style="left:612px;top:92px"><span>ABOUT US</span><svg width="18" height="10"><path d="M0 5H12M12 1V9M12 5H18" stroke="var(--navy)" stroke-width="2.5"/></svg></div>
  <div class="abs about-text">
    <h2>Welcome to Velqo Hydration</h2>
    <p>Velqo Hydration was established by a board-certified medical professional. We successfully integrate cutting-edge medical research with personalized IV nutritional therapy to provide our clients with the most effective and efficient treatment options.</p>
    <p>Gone are the days of relying solely on traditional medicine to address nutritional deficiencies and health concerns. At Velqo Hydration, we offer a unique and innovative approach to wellness, providing customized IV nutritional therapies in a relaxing and welcoming environment.</p>
    <p>Whether you're seeking relief from chronic fatigue, migraines, or digestive issues, or simply looking to boost your energy and immune system, our IV nutritional therapies can help. Our experienced medical team will work closely with you to create a personalized treatment plan tailored to your specific needs and health goals.</p>
  </div>
  <div class="btn">Book an Appointment</div>
</section>

<!-- SERVICES -->
<section class="services">
  <svg class="abs" style="left:0;top:-12px" width="1200" height="40" viewBox="0 0 1200 40" preserveAspectRatio="none"><path d="M0 40 L0 30 L200 26 L420 22 L640 18 L860 14 L1050 8 L1200 2 L1200 40Z" fill="var(--grey-bg)"/></svg>
  <div class="tag" style="left:0;width:1200px;top:86px"><span>OUR SERVICES</span><svg width="18" height="10"><path d="M0 5H12M12 1V9M12 5H18" stroke="var(--navy)" stroke-width="2.5"/></svg></div>
  <h2 class="section-title" style="top:118px">IV Treatment Programs</h2>

  <div class="card" style="left:116px;top:185px;background:linear-gradient(180deg,#b94a1c,#e0702a 45%,#2a160c)" role="img" aria-label="Silhouette of a man flexing against a sunset sky"><div class="label">Energy Boost IV</div></div>
  <div class="card feature" style="left:445px;top:185px">
    <div class="frame"></div>
    <svg class="abs" style="left:112px;top:56px" width="86" height="80" viewBox="0 0 86 80" fill="none" stroke="#fff" stroke-width="3"><circle cx="43" cy="14" r="9"/><path d="M43 26 C28 30 24 46 30 56 M43 26 C58 30 62 46 56 56 M4 48 C14 60 28 64 43 62 C58 64 72 60 82 48 M10 72 H76"/></svg>
    <div class="label" style="bottom:102px">Wellness IV</div>
    <svg class="abs" style="left:138px;top:195px" width="34" height="34"><circle cx="17" cy="17" r="16" fill="#fff"/><path d="M10 17H24M19 12L24 17L19 22" stroke="var(--navy)" stroke-width="1.8" fill="none"/></svg>
  </div>
  <div class="card" style="left:775px;top:185px;background:linear-gradient(160deg,#f4f2ee,#f3a12a 45%,#5a4a2c)" role="img" aria-label="Halved oranges and apples on a wooden board"><div class="label">Immunity IV</div></div>

  <div class="card" style="left:116px;top:485px;background:linear-gradient(90deg,#8a6a58,#c9aa95 50%,#b8b3ae)" role="img" aria-label="Split portrait comparing younger and older skin"><div class="label">Anti-Aging IV</div></div>
  <div class="card" style="left:445px;top:485px;background:linear-gradient(170deg,#eceae6,#d8d4cc 50%,#8b8f98)" role="img" aria-label="Woman measuring her waist with a tape measure"><div class="label">Weight Management IV</div></div>
  <div class="card" style="left:775px;top:485px;background:radial-gradient(circle at 45% 40%,#d23aa0,#2f3fb8 55%,#070a2a)" role="img" aria-label="Glowing illustration of a human brain"><div class="label">Brain Improvement IV</div></div>

  <div class="btn">View All Services</div>
  <svg class="abs" style="left:0;top:880px" width="1200" height="30" viewBox="0 0 1200 30" preserveAspectRatio="none"><path d="M0 30 L0 8 L300 14 L600 18 L900 22 L1200 24 L1200 30Z" fill="var(--white)"/></svg>
</section>

<!-- BENEFITS -->
<section class="benefits">
  <div class="tag" style="left:0;width:1200px;top:47px"><span>BENEFITS</span><svg width="18" height="10"><path d="M0 5H12M12 1V9M12 5H18" stroke="var(--navy)" stroke-width="2.5"/></svg></div>
  <h2 class="section-title" style="top:80px">Discover the Power of IV Nutrition</h2>
  <div class="abs" style="left:434px;top:140px;width:330px;height:436px;border-radius:165px;border:2px solid #cfe3ad;padding:10px">
    <div style="width:100%;height:100%;border-radius:155px;background:linear-gradient(180deg,#f2d7bd,#d9bfa8 45%,#7e7a78)" role="img" aria-label="Woman meditating seated facing the sea at sunrise"></div>
  </div>

  <div class="benefit left" style="left:0;top:186px;width:322px"><h4>Rapid Hydration</h4><p>Replenish essential fluids and<br>electrolytes to combat dehydration</p></div>
  <div class="icon-box" style="left:340px;top:184px"><svg width="32" height="32" viewBox="0 0 32 32" fill="none" stroke="var(--navy)" stroke-width="2"><circle cx="16" cy="17" r="11"/><circle cx="16" cy="17" r="5"/><path d="M16 2V6"/></svg></div>
  <div class="benefit left" style="left:0;top:309px;width:322px"><h4>Enhances Immune Function</h4><p>IV vitamins and minerals support<br>immune system function.</p></div>
  <div class="icon-box" style="left:340px;top:307px"><svg width="32" height="32" viewBox="0 0 32 32" fill="none" stroke="var(--navy)" stroke-width="2"><path d="M16 3L27 7V15C27 22 22 27 16 29C10 27 5 22 5 15V7Z"/><circle cx="16" cy="16" r="5"/></svg></div>
  <div class="benefit left" style="left:0;top:439px;width:322px"><h4>Reduced Stress and Anxiety</h4><p>Find calm and relaxation with specially<br>formulated infusions promoting</p></div>
  <div class="icon-box" style="left:340px;top:437px"><svg width="32" height="32" viewBox="0 0 32 32" fill="none" stroke="var(--navy)" stroke-width="2"><circle cx="16" cy="17" r="11"/><path d="M11 20C13 23 19 23 21 20M12 14H13M19 14H20"/></svg></div>

  <div class="icon-box" style="left:798px;top:184px"><svg width="32" height="32" viewBox="0 0 32 32" fill="none" stroke="var(--navy)" stroke-width="2"><circle cx="16" cy="16" r="12"/><path d="M18 7L11 17H16L14 25L21 15H16Z"/></svg></div>
  <div class="benefit" style="left:883px;top:186px"><h4>Boosts Energy</h4><p>IV nutrients help increase energy<br>levels and reduce fatigue.</p></div>
  <div class="icon-box" style="left:798px;top:307px"><svg width="32" height="32" viewBox="0 0 32 32" fill="none" stroke="var(--navy)" stroke-width="2"><circle cx="20" cy="6" r="3"/><path d="M9 12L16 10L20 14L16 20L22 26M16 20L10 26M20 14L26 16M3 16H9M5 21H11"/></svg></div>
  <div class="benefit" style="left:883px;top:309px"><h4>Improved Athletic Performance</h4><p>Optimize physical performance with<br>tailored amino acid infusions and</p></div>
  <div class="icon-box" style="left:798px;top:437px"><svg width="32" height="32" viewBox="0 0 32 32" fill="none" stroke="var(--navy)" stroke-width="2"><circle cx="16" cy="8" r="4"/><path d="M16 13C10 15 9 21 11 24M16 13C22 15 23 21 21 24M3 22C8 28 24 28 29 22M6 29H26"/></svg></div>
  <div class="benefit" style="left:883px;top:439px"><h4>Personalized Wellness</h4><p>Receive customized treatment plans<br>tailored to address specific health</p></div>
</section>

<!-- TESTIMONIALS -->
<section class="testimonials">
  <svg class="abs" style="left:0;top:-14px" width="1200" height="30" viewBox="0 0 1200 30" preserveAspectRatio="none"><path d="M0 30 L0 4 L300 8 L600 12 L900 14 L1200 16 L1200 30Z" fill="var(--green-soft)"/></svg>
  <div class="tag" style="left:0;width:1200px;top:50px"><span>TESTIMONIALS</span><svg width="18" height="10"><path d="M0 5H12M12 1V9M12 5H18" stroke="var(--navy)" stroke-width="2.5"/></svg></div>
  <h2 class="section-title" style="top:82px">What Our Customers Says About Us</h2>
  <div class="abs" style="left:116px;top:160px;width:350px;height:388px;border-radius:50%;background:linear-gradient(160deg,#9fc0d6,#5d7f72 50%,#3b4f2d)" role="img" aria-label="Woman holding a standing yoga pose on a mountain ledge"></div>
  <div class="abs" style="left:395px;top:300px;width:230px;height:230px;border-radius:50%;border:5px solid var(--white);background:linear-gradient(180deg,#f2f2f0,#d9d3cc 60%,#6f6b70)" role="img" aria-label="Woman meditating cross-legged in a bright room"></div>
  <svg class="abs" style="left:465px;top:210px" width="160" height="95" viewBox="0 0 160 95"><path d="M70 0 C30 8 8 38 12 70 C14 86 28 95 44 92 C58 89 66 76 62 62 C58 50 44 44 34 48 C38 28 52 14 72 8Z M150 0 C110 8 88 38 92 70 C94 86 108 95 124 92 C138 89 146 76 142 62 C138 50 124 44 114 48 C118 28 132 14 152 8Z" fill="var(--green)" transform="translate(160 0) scale(-1 1)"/></svg>
  <div class="abs" style="left:697px;top:196px;width:36px;height:36px;border-radius:50%;background:linear-gradient(#c8b6a8,#3a6aa8)" role="img" aria-label="Customer portrait"></div>
  <div class="abs" style="left:765px;top:186px;width:56px;height:56px;border-radius:50%;border:3px solid var(--green);background:linear-gradient(#e23a4a,#5a2a2a)" role="img" aria-label="Featured customer portrait"></div>
  <div class="abs" style="left:847px;top:196px;width:36px;height:36px;border-radius:50%;background:linear-gradient(#7a5a48,#c27040)" role="img" aria-label="Customer portrait"></div>
  <p class="abs quote-text">“I was skeptical at first, but after one session, I felt like a new person! My energy levels skyrocketed and I felt refreshed and rejuvenated. I noticed a significant improvement in my mental clarity, and I was able to focus and concentrate better. My stress and anxiety levels decreased, and I felt a sense of calm and relaxation that I hadn't experienced in a long time.”</p>
  <div class="abs person"><b>Marisol Quentin</b><small>Founder</small></div>
  <div class="arrow-btn" style="left:945px;top:500px;border:1.5px solid var(--navy)"><svg width="14" height="12"><path d="M13 6H2M6 1L1 6L6 11" stroke="var(--navy)" stroke-width="1.6" fill="none"/></svg></div>
  <div class="arrow-btn" style="left:991px;top:500px;border:1.5px solid var(--green)"><svg width="14" height="12"><path d="M1 6H12M8 1L13 6L8 11" stroke="var(--green)" stroke-width="1.6" fill="none"/></svg></div>
  <svg class="abs" style="left:0;top:628px" width="1200" height="24" viewBox="0 0 1200 24" preserveAspectRatio="none"><path d="M0 24 L0 14 L300 10 L600 8 L900 6 L1200 2 L1200 24Z" fill="var(--white)"/></svg>
</section>

<!-- BLOG -->
<section class="blog">
  <div class="tag" style="left:0;width:1200px;top:51px"><span>LATEST BLOGS</span><svg width="18" height="10"><path d="M0 5H12M12 1V9M12 5H18" stroke="var(--navy)" stroke-width="2.5"/></svg></div>
  <h2 class="section-title" style="top:86px">Check Out Our Daily Articles</h2>
  <article class="post" style="left:116px;top:153px">
    <div style="height:195px;background:linear-gradient(180deg,#e9a233,#f3c97a 40%,#d8d8d8)" role="img" aria-label="Orange IV drip bag hanging from a stand"></div>
    <span class="date">January 01</span>
    <h3>Revitalize Your Health: The Power of IV Nutritional Therapy</h3>
    <span class="more">READ MORE</span>
  </article>
  <article class="post" style="left:445px;top:153px">
    <div style="height:195px;background:linear-gradient(150deg,#e8eef4,#4a82d0 40%,#e9b070 70%,#cfd6dc)" role="img" aria-label="Gloved hands holding an IV bag filled with fruit"></div>
    <span class="date" style="background:var(--green)">January 05</span>
    <h3>Drip, Recharge, Repeat: The Benefits of IV Nutrition</h3>
    <span class="more" style="color:var(--green)">READ MORE</span>
  </article>
  <article class="post" style="left:775px;top:153px">
    <div style="height:195px;background:linear-gradient(150deg,#6a5a8a,#c7a48a 45%,#3e4a80)" role="img" aria-label="Nurse tending to a patient receiving an IV infusion"></div>
    <span class="date">January 10</span>
    <h3>The IV Advantage: How Nutritional Therapy Can Transform Your Health</h3>
    <span class="more">READ MORE</span>
  </article>
</section>

<!-- FOOTER -->
<footer class="site-footer">
  <svg class="abs" style="left:0;top:0" width="1200" height="30" viewBox="0 0 1200 30" preserveAspectRatio="none"><path d="M0 30 L0 24 L200 20 L420 16 L640 12 L860 10 L1050 6 L1200 2 L1200 30Z" fill="var(--footer)"/></svg>
  <div class="abs footer-bg"></div>
  <div class="abs footer-logo">VELQO</div>
  <div class="abs socials"><span></span><span></span><span></span></div>
  <div class="f-col" style="left:331px">
    <h5>NAVIGATION</h5>
    <ul><li>Home</li><li>About us</li><li>Services</li><li>Benefits</li><li>Blog</li><li>Contact Us</li></ul>
  </div>
  <div class="f-col therapy-list" style="left:555px">
    <h5>THERAPEUTIC SERVICES</h5>
    <ul><li>IV Antibiotics</li><li>Nutrition Support</li><li>Immunoglobulin</li><li>Chronic Inflammatory Disorders</li><li>Neurological Disorders</li><li>Bleeding Disorders</li><li>Women's Health</li><li>Heart Failure</li><li>Specialized Therapies</li></ul>
  </div>
  <div class="f-col" style="left:846px">
    <h5>CONTACT US</h5>
    <div class="contact-row"><svg width="16" height="20" viewBox="0 0 16 20" fill="none" stroke="#ddd" stroke-width="1.5"><path d="M8 19C8 19 15 12 15 7.5A7 7 0 0 0 1 7.5C1 12 8 19 8 19Z"/><circle cx="8" cy="7.5" r="2.5"/></svg><span>48 Alder Lane, Suite 210<br>Stockton, CA, USA</span></div>
    <div class="contact-row"><svg width="16" height="16" viewBox="0 0 16 16" fill="none" stroke="#ddd" stroke-width="1.5"><path d="M3 1L6 1L7 5L5 6.5C6 9 7 10 9.5 11L11 9L15 10V13C15 14 14 15 13 15C6 15 1 10 1 3C1 2 2 1 3 1Z"/></svg><span>555 014 2290</span></div>
    <div class="contact-row"><svg width="16" height="14" viewBox="0 0 16 14" fill="none" stroke="#ddd" stroke-width="1.5"><rect x="1" y="2" width="14" height="10"/><path d="M1 2L8 8L15 2"/></svg><span>contact@velqo.com</span></div>
  </div>
  <div class="abs copyright">© 2025 Velqo Hydration | All Rights Reserved.</div>
</footer>

</body>
</html>
```